brightwell - Property Management DL Card

I am after a savvy designer to cut through junk mail! so many real estate agents use flyers to promote themselves and their business and usually sales. We are a property management firm (residential) and we want to represent landlords that have existing investment properties and need a quality agent to represent them. Can you help?
DL size, will be printed and delivered to mailboxes. For a look at our website go to www.brightwellrs.com.au. Keep it simple and clutter free.
it is to be double sided - with one side to be simple and clear - just our website, logo and telephone number on the back.
attached is our logo and our telephone number is 1300 48 92 16
the above are 2 essential elements to be included + our email address: admin@brightwellrs.com.au
also attached are our transparent price list

Target Market(s)
property investors,
people that manage properties themselves
Industry/Entity Type
Property Management
- arial
Look and feel

```html
<!DOCTYPE html>
<html lang="en">
<head>
<meta charset="utf-8">
<title>brightwell – Property Management DL Card</title>
<link rel="stylesheet" href="https://fonts.googleapis.com/css2?family=Open+Sans:wght@300;400;600&display=swap">
<style>
  :root {
    --backdrop: #c9cac8;
    --card-back: #e2e1dd;
    --plum: #5a3558;
    --plum-deep: #3f2440;
    --plum-text: #6a2a6a;
    --ink: #222222;
    --ink-soft: #333333;
    --white: #ffffff;
  }
  * { margin: 0; padding: 0; box-sizing: border-box; }
  html, body {
    width: 1200px; height: 1200px; overflow: hidden;
    background: var(--backdrop);
    font-family: "Open Sans", Arial, sans-serif;
  }
  .canvas { position: relative; width: 1200px; height: 1200px; }

  .card { position: absolute; left: 121px; width: 1000px; height: 500px; overflow: hidden; }
  .card--front { top: 55px; }
  .card--back { top: 636px; background: var(--card-back); }

  .interior-photo {
    position: absolute; inset: 0;
    background:
      radial-gradient(ellipse 45% 18% at 50% 62%, rgba(178,206,74,0.95), rgba(178,206,74,0) 100%),
      linear-gradient(90deg, rgba(120,126,118,0.55) 0%, rgba(0,0,0,0) 22%, rgba(0,0,0,0) 78%, rgba(236,238,232,0.6) 100%),
      linear-gradient(180deg, #7f827b 0%, #a4a69d 25%, #e6e6e0 45%, #c7c9bc 62%, #b89763 80%, #a07a45 100%);
  }

  .front-logo {
    position: absolute; left: 376px; top: 65px; width: 268px; height: 66px;
    background: rgba(20,20,20,0.82);
    display: flex; align-items: center; justify-content: center;
  }
  .brand-name {
    font-weight: 300; font-size: 38px; color: var(--white); letter-spacing: 0.5px; line-height: 1;
  }

  .benefits-band {
    position: absolute; left: 0; top: 403px; width: 1000px; height: 97px;
    background: rgba(90,53,88,0.88);
  }
  .benefits-band__tagline {
    position: absolute; left: 0; top: 14px; width: 1000px; height: 30px;
    background: linear-gradient(90deg, rgba(63,36,64,0) 0%, rgba(63,36,64,0.7) 25%, rgba(63,36,64,0.7) 75%, rgba(63,36,64,0) 100%);
    color: var(--white); font-size: 19px; font-weight: 300;
    text-align: center; line-height: 30px;
  }
  .benefits-list {
    position: absolute; left: 0; top: 56px; width: 1000px;
    display: flex; justify-content: center; gap: 22px;
    list-style: none; color: var(--white); font-size: 15px; font-weight: 400;
  }
  .benefits-list .divider { opacity: 0.8; }

  .back-logo {
    position: absolute; left: 314px; top: 160px; width: 370px; height: 61px;
    background: linear-gradient(90deg, rgba(90,53,88,0) 0%, var(--plum-deep) 22%, var(--plum) 70%, rgba(90,53,88,0) 100%);
    display: flex; align-items: center; justify-content: center;
  }
  .back-logo .brand-name { font-size: 34px; }

  .contact {
    position: absolute; left: 0; top: 241px; width: 1000px;
    text-align: center; font-style: normal; color: var(--ink);
  }
  .contact__line { display: block; font-size: 17px; line-height: 24px; }
  .contact__phone { display: block; font-size: 20px; font-weight: 600; color: var(--ink-soft); line-height: 30px; letter-spacing: 0.5px; }
  .contact__web { color: var(--plum-text); }
</style>
</head>
<body>
<main class="canvas">
  <section class="card card--front">
    <div class="interior-photo" role="img" aria-label="Photograph of a bright modern lounge with a lime green modular sofa, glass table, potted plants, timber floor and window blinds"></div>
    <div class="front-logo"><span class="brand-name">brightwell</span></div>
    <div class="benefits-band">
      <p class="benefits-band__tagline">Property Management specialists</p>
      <ul class="benefits-list">
        <li>No postage and admin fees</li>
        <li class="divider">|</li>
        <li>No hidden extras</li>
        <li class="divider">|</li>
        <li>Excellent communication</li>
        <li class="divider">|</li>
        <li>Technology focussed</li>
      </ul>
    </div>
  </section>

  <section class="card card--back">
    <div class="back-logo"><span class="brand-name">brightwell</span></div>
    <address class="contact">
      <span class="contact__line">PO Box C512, Harbourside NSW, 2999</span>
      <span class="contact__phone">1.300.48.92.16</span>
      <span class="contact__line">admin@brightwellrs.com.au</span>
      <span class="contact__line contact__web">www.brightwellrs.com.au</span>
    </address>
  </section>
</main>
</body>
</html>
```